Property Services Company Needs a Brochure Design

Looking for a new brochure design for an existing property services company.

We provide a range of property services from, market research, real estate brokerage, valuation and appraisal, property development and other real estate consulting services.

We would like a fresh modern brochure design with good graphics and features. Our colours are white, blue and orange.

The design should communicate, attention to detail, superior service delivery and distinction in results.
Updates

I would like the brochure to be roughly about 20 pages.

Containing the following,

1) An introduction
2) Contents Page
2) What we do
3) Our Services
4) Agency & Brokerage
5) Real Estate Consulting
6) Market Research
7) Appraisal & Valuation
8) Project Management
9) Property Development

I would also like icons to represent items 4,5,6,7,8 & 9, they should be represented vertically on each of the pages from the contents page and highlighted individually on the pages that they represent.. i.e. on appraisal & valuation page, all six icons will be arranged vertically and the appraisal and valuations icon will be highlighted.

I will also like to have images that depict the services on the various pages.

I have some pages I think will flow which I will upload shortly.

Industry/Entity Type

Real Estate

Font styles to use
Serif

Colors
f78f20
0455a3

```html
<!DOCTYPE html>
<html lang="en">
<head>
<meta charset="utf-8">
<title>Brochure Spreads – Pages 11 to 14</title>
<link href="https://fonts.googleapis.com/css2?family=Open+Sans:ital,wght@0,300;0,400;0,600;1,400;1,600;1,700&display=swap" rel="stylesheet">
<style>
  :root {
    --orange: #f78f20;
    --orange-deep: #d4731a;
    --blue: #0a3a78;
    --blue-deep: #072a58;
    --ink: #333333;
    --ink-soft: #555555;
    --paper: #f4f4f4;
    --paper-edge: #cfcfcf;
    --stage: #232323;
    --icon-grey: #6a6a6a;
  }
  * { margin: 0; padding: 0; box-sizing: border-box; }
  html, body { width: 1200px; height: 900px; overflow: hidden; }
  body {
    background: radial-gradient(ellipse at 50% 40%, #3a3a3a 0%, var(--stage) 60%, #151515 100%);
    font-family: "Open Sans", Arial, sans-serif;
    position: relative;
  }
  .spread-label {
    position: absolute;
    left: 0; width: 1200px;
    text-align: center;
    color: #ffffff;
    font-style: italic;
    font-size: 19px;
    font-weight: 400;
  }
  .spread {
    position: absolute;
    left: 121px;
    width: 936px;
    height: 331px;
    background: radial-gradient(ellipse at 30% 15%, #ffffff 0%, var(--paper) 40%, var(--paper-edge) 100%);
    box-shadow: 0 4px 10px rgba(0,0,0,0.7);
    overflow: hidden;
  }
  .spread svg.shapes { position: absolute; left: 0; top: 0; }
  .header-title {
    position: absolute;
    top: 16px;
    color: #ffffff;
    font-size: 15px;
    font-weight: 300;
    letter-spacing: 0.3px;
  }
  .body-copy {
    position: absolute;
    color: var(--ink-soft);
    font-size: 9.4px;
    line-height: 17.5px;
  }
  .body-copy p + p { margin-top: 9px; }
  .service-photo {
    position: absolute;
    left: 469px; top: 122px;
    width: 258px; height: 209px;
    background: linear-gradient(160deg, #6d9ac9 0%, #9bb8d6 35%, #a08a5c 60%, #3d4a57 100%);
  }
  .team-statement {
    position: absolute;
    left: 40px; top: 90px;
    width: 370px;
    text-align: right;
    color: #1c1c1c;
    font-style: italic;
    font-size: 15px;
    line-height: 16px;
  }
  .team-statement p + p { margin-top: 16px; }
  .web-address {
    position: absolute;
    right: 30px; top: 127px;
    color: var(--orange-deep);
    font-style: italic;
    font-weight: 700;
    font-size: 17px;
  }
</style>
</head>
<body>

  <div class="spread-label" style="top:20px;">page 11-12</div>

  <section class="spread" style="top:67px;" aria-label="Pages 11 and 12">
    <svg class="shapes" width="936" height="331" viewBox="0 0 936 331">
      <defs>
        <linearGradient id="headerGrad" x1="0" x2="1" y1="0" y2="0">
          <stop offset="0" stop-color="#c96a12"/>
          <stop offset="1" stop-color="var(--orange)"/>
        </linearGradient>
        <linearGradient id="blueGrad" x1="0" x2="1" y1="0" y2="1">
          <stop offset="0" stop-color="#0c4386"/>
          <stop offset="1" stop-color="var(--blue-deep)"/>
        </linearGradient>
      </defs>
      <rect x="0" y="0" width="26" height="331" fill="url(#blueGrad)"/>
      <rect x="26" y="0" width="443" height="48" fill="url(#headerGrad)"/>
      <rect x="562" y="0" width="374" height="48" fill="url(#headerGrad)"/>
      <polygon points="469,0 505,0 571,68 469,174" fill="url(#blueGrad)"/>
      <line x1="505" y1="0" x2="571" y2="68" stroke="var(--orange-deep)" stroke-width="3"/>
      <polygon points="571,70 854,331 319,331" fill="url(#blueGrad)"/>
      <polyline points="311,331 571,61 862,331" fill="none" stroke="var(--orange-deep)" stroke-width="4"/>
      <!-- project management icon -->
      <rect x="39" y="0" width="93" height="124" fill="var(--orange-deep)"/>
      <rect x="47" y="27" width="78" height="77" rx="12" fill="#eeeeee"/>
      <g fill="none" stroke="var(--orange-deep)" stroke-width="6" stroke-linecap="round">
        <path d="M70 60 A17 17 0 0 1 100 56"/>
        <path d="M102 71 A17 17 0 0 1 72 75"/>
      </g>
      <polygon points="96,48 108,56 96,63" fill="var(--orange-deep)"/>
      <polygon points="76,84 64,76 76,69" fill="var(--orange-deep)"/>
      <polyline points="86,55 86,66 93,70" fill="none" stroke="var(--orange-deep)" stroke-width="3.5" stroke-linecap="round"/>
      <!-- property development icon -->
      <rect x="834" y="48" width="93" height="77" fill="var(--orange-deep)"/>
      <g fill="var(--icon-grey)">
        <rect x="849" y="90" width="9" height="10"/>
        <rect x="862" y="80" width="9" height="20"/>
        <rect x="875" y="86" width="9" height="14"/>
        <rect x="888" y="72" width="9" height="28"/>
      </g>
      <polyline points="851,78 866,64 879,72 903,43" fill="none" stroke="var(--icon-grey)" stroke-width="4"/>
      <polygon points="898,38 910,35 908,48" fill="var(--icon-grey)"/>
    </svg>

    <div class="header-title" style="left:243px;">PROJECT MANAGEMENT</div>
    <div class="header-title" style="left:589px;">PROPERTY DEVELOPEMENT</div>

    <div class="body-copy" style="left:46px; top:141px; width:400px;">
      <p>Our project management team, with vast experience across commercial and residential developments provide the much needed support to achieve your dream property or office, allowing our clients to concentrate on their core business.</p>
      <p>We provide accurate information from financing, to design concept to budgeting and construction management.</p>
    </div>

    <div class="service-photo" role="img" aria-label="Photo of three site engineers in hard hats and safety vests reviewing building plans"></div>

    <div class="body-copy" style="right:12px; top:141px; width:236px; text-align:right;">
      <p>We take pride in creating inspirational developments that people can live, work and enjoy, whilst adding value.</p>
    </div>
  </section>

  <div class="spread-label" style="top:434px;">page 13-14</div>

  <section class="spread" style="top:469px;" aria-label="Pages 13 and 14">
    <svg class="shapes" width="936" height="331" viewBox="0 0 936 331">
      <defs>
        <linearGradient id="blueGrad2" x1="0" x2="1" y1="0" y2="1">
          <stop offset="0" stop-color="#0c4386"/>
          <stop offset="1" stop-color="var(--blue-deep)"/>
        </linearGradient>
      </defs>
      <rect x="0" y="0" width="26" height="331" fill="url(#blueGrad2)"/>
      <polygon points="469,0 505,0 571,68 469,174" fill="url(#blueGrad2)"/>
      <line x1="505" y1="0" x2="571" y2="68" stroke="var(--orange-deep)" stroke-width="3"/>
      <polygon points="571,70 854,331 319,331" fill="url(#blueGrad2)"/>
      <polyline points="311,331 571,61 862,331" fill="none" stroke="var(--orange-deep)" stroke-width="4"/>
    </svg>

    <div class="team-statement">
      <p>We have a commited team of professionals accross all business units that provides a unique integrated service support approach.</p>
      <p>They deliver using industry best practices at a competitive rates.</p>
    </div>

    <div class="web-address">www.harrowgate.com.ng</div>
  </section>

</body>
</html>
```